UI/ UX Design for ERP Software

We need a new UX/UI interface for a ERP software for property managers. Our CMMS / ERP solution is made based on responsive design technologies and is coded in PHP.
The overall UX to be similar to Tev Ulna - easy navigation, intuitive menus.

Industry/Entity Type

Property Management

Number of Pages Required

5+ page

Requirements
Must have
• Round dock buttons
Consistent icons across the application
Enough Spacing between buttons/icons/ menu
Consistent Font
Nice to have
• We would like the UX to allow the users to use the application without /minimum training.
Should not have
• we don't want anything that is classic with respect to UX

```html
<!DOCTYPE html>
<html lang="en">
<head>
<meta charset="utf-8">
<title>Domora – Active Dashboard</title>
<link rel="stylesheet" href="https://fonts.googleapis.com/css2?family=Lato:wght@400;700;900&display=swap">
<style>
:root{
  --ink:#3b3f45;
  --brand:#1a56c4;
  --side:#434f5c;
  --side-text:#ffffff;
  --page:#f0f0f0;
  --tab-off:#c9c9c9;
  --panel:#ffffff;
  --grid:#d6d6d6;
  --c1:#1ba6e6;--c2:#3a9a1c;--c3:#f47b13;--c4:#4a4a4a;--c5:#9b66e0;--c6:#ec3a66;--c7:#f5b10c;
}
*{box-sizing:border-box;margin:0;padding:0}
html,body{width:1200px;height:861px;overflow:hidden}
body{font-family:"Lato",sans-serif;color:var(--ink);background:var(--page);position:relative}
.topbar{position:absolute;left:0;top:0;width:1200px;height:84px;background:#fff}
.brand{position:absolute;left:34px;top:26px;display:flex;align-items:center;gap:9px}
.brand-mark{width:18px;height:18px;border-radius:50%;background:var(--ink)}
.brand-name{font-size:26px;font-weight:400;color:var(--ink);letter-spacing:.5px}
.divider{position:absolute;left:209px;top:18px;width:1px;height:48px;background:#888}
.page-title{position:absolute;left:222px;top:34px;display:flex;align-items:center;gap:10px;font-size:12.5px;letter-spacing:.3px}
.stat{position:absolute;top:31px}
.stat-label{display:flex;align-items:center;gap:8px;font-size:10.5px;letter-spacing:.2px;white-space:nowrap}
.stat-value{font-size:12.5px;color:var(--brand);margin-top:6px;font-weight:400;white-space:nowrap}
.sidebar{position:absolute;left:0;top:84px;width:210px;height:777px;background:var(--side)}
.nav-item{position:absolute;left:0;width:210px;height:20px;display:flex;align-items:center;color:var(--side-text);font-size:8px;font-weight:700;letter-spacing:.4px}
.nav-item .ico{position:absolute;left:13px;width:10px;height:10px;fill:#fff}
.nav-item .label{position:absolute;left:35px}
.nav-item .expand{position:absolute;left:191px;width:8px;height:8px;border:1px solid #fff;border-radius:1px}
.nav-item .expand::before,.nav-item .expand::after{content:"";position:absolute;background:#fff}
.nav-item .expand::before{left:1px;right:1px;top:2.5px;height:1px}
.nav-item .expand::after{top:1px;bottom:1px;left:2.5px;width:1px}
.tab{position:absolute;top:129px;width:144px;height:34px;display:flex;align-items:center;justify-content:center;gap:10px;font-size:11px;font-weight:400;color:#fff;background:var(--tab-off);letter-spacing:.2px}
.tab.active{background:var(--panel);color:var(--brand);font-weight:900}
.panel{position:absolute;left:222px;top:163px;width:959px;height:362px;background:var(--panel)}
.range{position:absolute;left:18px;top:34px;display:flex;align-items:center;gap:13px;font-size:11px;font-weight:700;color:#444}
.chart{position:absolute;left:0;top:0}
.legend{position:absolute;left:30px;top:324px}
.legend-item{position:absolute;display:flex;align-items:center;gap:6px;font-size:6.5px;white-space:nowrap;color:#333}
.legend-item i{display:block;width:11px;height:11px}
</style>
</head>
<body>
<header class="topbar">
  <div class="brand"><span class="brand-mark"></span><span class="brand-name">Domora</span></div>
  <div class="divider"></div>
  <div class="page-title">
    <svg width="14" height="12" viewBox="0 0 14 12"><path d="M7 0L0 6h2v6h4V8h2v4h4V6h2z" fill="#555"/></svg>
    ACTIVE DASHBOARD
  </div>
  <div class="stat" style="left:572px"><div class="stat-label"><svg width="13" height="11" viewBox="0 0 14 12"><path d="M7 0L0 6h2v6h4V8h2v4h4V6h2z" fill="#555"/></svg>PROPERTIES</div><div class="stat-value" style="padding-left:22px">3</div></div>
  <div class="stat" style="left:678px"><div class="stat-label"><svg width="15" height="10" viewBox="0 0 15 10"><circle cx="7.5" cy="3" r="2.5" fill="#555"/><circle cx="2.5" cy="3.5" r="1.8" fill="#555"/><circle cx="12.5" cy="3.5" r="1.8" fill="#555"/><path d="M3 10a4.5 4.5 0 019 0zM0 9a2.5 2.5 0 014-2M15 9a2.5 2.5 0 00-4-2" fill="#555"/></svg>TENANTS</div><div class="stat-value" style="padding-left:21px">8</div></div>
  <div class="stat" style="left:768px"><div class="stat-label"><svg width="11" height="11" viewBox="0 0 11 11"><path d="M0 0h4L0 4zM11 0v4L7 0zM0 11V7l4 4zM11 11H7l4-4zM2 2l7 7M9 2L2 9" stroke="#555" stroke-width="1.6" fill="#555"/></svg>TOTAL PROPERTIES AREA</div><div class="stat-value" style="padding-left:22px">422,000.00 sq.ft.</div></div>
  <div class="stat" style="left:938px"><div class="stat-label"><svg width="11" height="11" viewBox="0 0 11 11"><path d="M0 0h4L0 4zM11 0v4L7 0zM0 11V7l4 4zM11 11H7l4-4zM2 2l7 7M9 2L2 9" stroke="#555" stroke-width="1.6" fill="#555"/></svg>RENTED AREA</div><div class="stat-value" style="padding-left:23px">233,500.00 sq.ft</div></div>
  <div class="stat" style="left:1067px"><div class="stat-label"><svg width="11" height="11" viewBox="0 0 11 11"><path d="M0 0h4L0 4zM11 0v4L7 0zM0 11V7l4 4zM11 11H7l4-4zM2 2l7 7M9 2L2 9" stroke="#555" stroke-width="1.6" fill="#555"/></svg>VACANCIES AREA</div><div class="stat-value" style="padding-left:22px">188,500.00 sq.ft</div></div>
</header>

<nav class="sidebar">
  <div class="nav-item" style="top:23px"><svg class="ico" viewBox="0 0 10 10"><path d="M0 8a5 5 0 0110 0z"/></svg><span class="label">DASHBOARD</span></div>
  <div class="nav-item" style="top:55px"><svg class="ico" viewBox="0 0 10 10"><circle cx="5" cy="3" r="2"/><path d="M1 9a4 4 0 018 0z"/></svg><span class="label">CUSTOMERS</span></div>
  <div class="nav-item" style="top:87px"><svg class="ico" viewBox="0 0 10 10"><path d="M5 0L0 5h1.5v5h7V5H10z"/></svg><span class="label">PROPERTIES</span></div>
  <div class="nav-item" style="top:119px"><svg class="ico" viewBox="0 0 10 10"><circle cx="5" cy="5" r="5"/></svg><span class="label">TENANTS</span></div>
  <div class="nav-item" style="top:151px"><svg class="ico" viewBox="0 0 10 10"><path d="M2 0h4l3 3v7H2z"/></svg><span class="label">CONTACTS</span></div>
  <div class="nav-item" style="top:183px"><svg class="ico" viewBox="0 0 10 10"><circle cx="5" cy="3" r="2.5"/><path d="M1 10a4 4 0 018 0z"/></svg><span class="label">CONTRACTORS</span></div>
  <div class="nav-item" style="top:215px"><svg class="ico" viewBox="0 0 10 10"><circle cx="3" cy="3" r="2"/><circle cx="7" cy="3" r="2"/><path d="M0 9a3 3 0 0110 0z"/></svg><span class="label">EMPLOYEES</span></div>
  <div class="nav-item" style="top:247px"><svg class="ico" viewBox="0 0 10 10"><path d="M2 0h4l3 3v7H2z"/></svg><span class="label">COMPLIANCE MANAGEMENT</span></div>
  <div class="nav-item" style="top:279px"><svg class="ico" viewBox="0 0 10 10"><circle cx="4" cy="5" r="3"/><circle cx="8.5" cy="2" r="1.5"/></svg><span class="label">PREVENT MAINTENANCE</span><span class="expand"></span></div>
  <div class="nav-item" style="top:311px"><svg class="ico" viewBox="0 0 10 10"><path d="M2 0h4l3 3v7H2z"/></svg><span class="label">WORK ORDERS</span><span class="expand"></span></div>
  <div class="nav-item" style="top:343px"><svg class="ico" viewBox="0 0 10 10"><path d="M2 0h4l3 3v7H2z"/></svg><span class="label">PURCHASE ORDERS</span></div>
  <div class="nav-item" style="top:375px"><svg class="ico" viewBox="0 0 10 10"><circle cx="4" cy="4" r="3" fill="none" stroke="#fff" stroke-width="1.6"/><path d="M6 6l3.5 3.5" stroke="#fff" stroke-width="1.8"/></svg><span class="label">PROPERTY INSPECTIONS</span><span class="expand"></span></div>
  <div class="nav-item" style="top:407px"><svg class="ico" viewBox="0 0 10 10"><path d="M0 1h1v8h9v1H0zM2 5h1v3H2zM4 3h1v5H4zM6 4h1v4H6zM8 2h1v6H8z"/></svg><span class="label">ENERGY MANAGEMENT</span></div>
  <div class="nav-item" style="top:439px"><svg class="ico" viewBox="0 0 10 10"><circle cx="5" cy="5" r="5"/></svg><span class="label">RISK MANAGEMENT</span></div>
  <div class="nav-item" style="top:471px"><svg class="ico" viewBox="0 0 10 10"><path d="M0 1h10v2H0zM0 4h10v2H0zM0 7h10v2H0z"/></svg><span class="label">PROJECT MANAGEMENT</span></div>
  <div class="nav-item" style="top:503px"><svg class="ico" viewBox="0 0 10 10"><path d="M0 2h10v6H0z"/></svg><span class="label">FINANCIAL - BUDGETING</span></div>
  <div class="nav-item" style="top:535px"><svg class="ico" viewBox="0 0 10 10"><ellipse cx="4" cy="4" rx="4" ry="3"/><ellipse cx="7" cy="7" rx="3" ry="2.2"/></svg><span class="label">TENANT REQUESTS</span></div>
  <div class="nav-item" style="top:567px"><svg class="ico" viewBox="0 0 10 10"><path d="M5 0v5h5A5 5 0 115 0z"/></svg><span class="label">REPORTS</span><span class="expand"></span></div>
  <div class="nav-item" style="top:599px"><svg class="ico" viewBox="0 0 10 10"><path d="M0 1h1v8h9v1H0zM2 8l2-4 2 2 3-4v6z"/></svg><span class="label">VISUAL REPORTS</span></div>
  <div class="nav-item" style="top:631px"><svg class="ico" viewBox="0 0 10 10"><path d="M2 0h6v8H2zM0 2h1v8h6v-1H1z"/></svg><span class="label">FILES</span></div>
  <div class="nav-item" style="top:663px"><svg class="ico" viewBox="0 0 10 10"><path d="M2 0h6v8H2zM0 2h1v8h6v-1H1z"/></svg><span class="label">PAGES</span><span class="expand"></span></div>
  <div class="nav-item" style="top:695px"><svg class="ico" viewBox="0 0 10 10"><circle cx="5" cy="5" r="4"/><circle cx="5" cy="5" r="1.5" fill="#434f5c"/></svg><span class="label">CONFIGURATIONS</span><span class="expand"></span></div>
  <div class="nav-item" style="top:727px"><svg class="ico" viewBox="0 0 10 10"><path d="M0 9l6-6 1 1-6 6zM6 1a2 2 0 113 3z"/></svg><span class="label">SETTINGS</span><span class="expand"></span></div>
</nav>

<div class="tab active" style="left:222px"><svg width="11" height="11" viewBox="0 0 11 11"><circle cx="5.5" cy="5.5" r="4.6" fill="none" stroke="currentColor" stroke-width="1.3"/><path d="M5.5 3v3h2" fill="none" stroke="currentColor" stroke-width="1.2"/></svg>LAST 7 DAYS</div>
<div class="tab" style="left:371px"><svg width="11" height="11" viewBox="0 0 11 11"><circle cx="5.5" cy="5.5" r="4.6" fill="none" stroke="currentColor" stroke-width="1.3"/><path d="M5.5 3v3h2" fill="none" stroke="currentColor" stroke-width="1.2"/></svg>LAST MONTHS</div>
<div class="tab" style="left:519px"><svg width="11" height="11" viewBox="0 0 11 11"><circle cx="5.5" cy="5.5" r="4.6" fill="none" stroke="currentColor" stroke-width="1.3"/><path d="M5.5 3v3h2" fill="none" stroke="currentColor" stroke-width="1.2"/></svg>LAST 3 MONTHS</div>
<div class="tab" style="left:667px"><svg width="11" height="11" viewBox="0 0 11 11"><circle cx="5.5" cy="5.5" r="4.6" fill="none" stroke="currentColor" stroke-width="1.3"/><path d="M5.5 3v3h2" fill="none" stroke="currentColor" stroke-width="1.2"/></svg>NEXT 7 DAYS</div>
<div class="tab" style="left:815px"><svg width="11" height="11" viewBox="0 0 11 11"><circle cx="5.5" cy="5.5" r="4.6" fill="none" stroke="currentColor" stroke-width="1.3"/><path d="M5.5 3v3h2" fill="none" stroke="currentColor" stroke-width="1.2"/></svg>NEXT MONTHS</div>
<div class="tab" style="left:964px"><svg width="11" height="11" viewBox="0 0 11 11"><circle cx="5.5" cy="5.5" r="4.6" fill="none" stroke="currentColor" stroke-width="1.3"/><path d="M5.5 3v3h2" fill="none" stroke="currentColor" stroke-width="1.2"/></svg>NEXT 3 MONTHS</div>

<section class="panel">
  <div class="range"><svg width="13" height="10" viewBox="0 0 13 10"><path d="M0 8h2v2H0zM3 6h2v4H3zM6 4h2v6H6zM9 2h2v8H9zM12 0h1v10h-1z" fill="#555"/></svg>12/27/2020 - 01/03/2021</div>
  <svg class="chart" width="959" height="362" viewBox="0 0 959 362" font-family="Lato, sans-serif">
    <g fill="#555"><rect x="18" y="77" width="10" height="1.5"/><rect x="18" y="80.5" width="10" height="1.5"/><rect x="18" y="84" width="10" height="1.5"/></g>
    <g stroke="var(--grid)" stroke-width="1">
      <line x1="71" y1="80.5" x2="887" y2="80.5"/><line x1="71" y1="118.5" x2="887" y2="118.5"/>
      <line x1="71" y1="156.5" x2="887" y2="156.5"/><line x1="71" y1="193.5" x2="887" y2="193.5"/>
      <line x1="71" y1="231.5" x2="887" y2="231.5"/>
    </g>
    <line x1="71" y1="269.5" x2="887" y2="269.5" stroke="#aaa"/>
    <g stroke="#aaa">
      <line x1="71.5" y1="269" x2="71.5" y2="287"/><line x1="173.5" y1="269" x2="173.5" y2="287"/>
      <line x1="275.5" y1="269" x2="275.5" y2="287"/><line x1="377.5" y1="269" x2="377.5" y2="287"/>
      <line x1="479.5" y1="269" x2="479.5" y2="287"/><line x1="581.5" y1="269" x2="581.5" y2="287"/>
      <line x1="683.5" y1="269" x2="683.5" y2="287"/><line x1="785.5" y1="269" x2="785.5" y2="287"/>
      <line x1="887.5" y1="269" x2="887.5" y2="287"/>
    </g>
    <g font-size="10.5" fill="#333" text-anchor="end">
      <text x="63" y="84">1.25</text><text x="63" y="121">1</text><text x="63" y="158">0.75</text>
      <text x="63" y="194">0.5</text><text x="63" y="231">0.25</text><text x="63" y="267">0</text>
    </g>
    <rect x="425" y="80" width="9" height="189" fill="var(--c1)"/>
    <g font-size="9.5" fill="#444" text-anchor="middle">
      <text x="120" y="283">12/27/2020</text><text x="224" y="283">12/28/2020</text>
      <text x="328" y="283">12/29/2020</text><text x="426" y="283">12/30/2020</text>
      <text x="530" y="283">12/31/2020</text><text x="631" y="283">01/01/2021</text>
      <text x="731" y="283">01/03/2021</text><text x="834" y="283">01/02/2021</text>
    </g>
  </svg>
  <div class="legend">
    <div class="legend-item" style="left:0"><i style="background:var(--c1)"></i>SCHEDULED MAINTENANCE</div>
    <div class="legend-item" style="left:115px"><i style="background:var(--c2)"></i>COMPLETED SCHEDULED MAINTENANCE</div>
    <div class="legend-item" style="left:274px"><i style="background:var(--c3)"></i>FUTURE SCHEDULED MAINTENANCE</div>
    <div class="legend-item" style="left:417px"><i style="background:var(--c4)"></i>SCHEDULED WORK ORDERS</div>
    <div class="legend-item" style="left:532px"><i style="background:var(--c5)"></i>COMPLETED WORK ORDERS</div>
    <div class="legend-item" style="left:647px"><i style="background:var(--c6)"></i>PROPERTY INSPECTIONS</div>
    <div class="legend-item" style="left:751px"><i style="background:var(--c7)"></i>COMPLETED PROPERTY INSPECTIONS</div>
  </div>
</section>
</body>
</html>
```